Electrical Contractor Brochure, Folder and Letter Head

Brightwell Power Ltd. is an Edmonton based electrical contractor focusing on commercial and industrial electrical services. Our target market is manufacturing facilities, warehouses and commercial buildings.

We want to seem larger than we are with service vehicles and electricians ready to dispatch to service calls and new installations. Our key color is the blue in the logo. The BWP logo is well branded in Edmonton and should be on the brochure.

We are looking for a tri-fold brochure, full-page brochure with folder sleeves and a letter head.
Updates

Please ignore the second page of copy.  I only want the electrical content in the brochure.  This is my mistake.  Please use only the first page of copy.

Industry/Entity Type

Electrical

Requirements
Must have
• Many background pics of the services, electricians and projects. I like the faded BWP logo in the background of the letterhead! Folder Size A4
Nice to have
• Try the pic named Cover Pic1 to on the front of the brochure.
Should not have
• DO NOT USE ANY WEBSITE CONTENT. THIS IS NOT OUR BUSINESS. PLEASE USE ONLY CONTENT AND COLOR FROM THE ATTACHED FILES!!

```html
<!DOCTYPE html>
<html lang="en">
<head>
<meta charset="utf-8">
<title>Brightwell Power Ltd. — Letterhead</title>
<link href="https://fonts.googleapis.com/css2?family=Source+Sans+3:wght@400;700&display=swap" rel="stylesheet">
<style>
  :root {
    --brand-blue: #1561ad;
    --deep-blue: #1b3a8c;
    --band-grey: #7a7a7a;
    --ink: #333333;
    --rule: #bdbdbd;
    --paper: #ffffff;
  }
  html, body {
    margin: 0;
    padding: 0;
    overflow: hidden;
    background: var(--paper);
  }
  .letterhead {
    position: relative;
    width: 1011px;
    height: 1200px;
    background: var(--paper);
    font-family: "Source Sans 3", "Myriad Pro", sans-serif;
    color: var(--ink);
    overflow: hidden;
  }
  .brand {
    position: absolute;
    left: 54px;
    top: 92px;
    display: flex;
    align-items: center;
    gap: 14px;
  }
  .brand-mark {
    width: 34px;
    height: 34px;
    background: var(--deep-blue);
  }
  .brand-name {
    font-weight: 700;
    font-size: 31px;
    color: var(--deep-blue);
    letter-spacing: 0.3px;
    white-space: nowrap;
  }
  .address {
    position: absolute;
    right: 222px;
    top: 99px;
    text-align: right;
    font-size: 16px;
    line-height: 18px;
  }
  .divider {
    position: absolute;
    left: 811px;
    top: 102px;
    width: 1px;
    height: 81px;
    background: var(--rule);
  }
  .contact-list {
    position: absolute;
    left: 826px;
    top: 78px;
    margin: 0;
    padding: 0;
    list-style: none;
    font-size: 16px;
    line-height: 19.5px;
  }
  .contact-list li {
    display: flex;
    align-items: center;
    gap: 5px;
  }
  .contact-icon {
    width: 11px;
    height: 11px;
    fill: var(--brand-blue);
    flex: none;
  }
  .footer-band {
    position: absolute;
    left: 0;
    bottom: 0;
    width: 1011px;
    height: 21px;
  }
</style>
</head>
<body>
<main class="letterhead">
  <header>
    <div class="brand">
      <span class="brand-mark"></span>
      <span class="brand-name">Brightwell Power Ltd.</span>
    </div>

    <address class="address" style="font-style:normal">
      00, complex name<br>City, state
    </address>

    <div class="divider"></div>

    <ul class="contact-list">
      <li>
        <svg class="contact-icon" viewBox="0 0 12 12" aria-label="Phone"><circle cx="6" cy="6" r="5.5" fill="none" stroke="var(--brand-blue)" stroke-width="1"/><path d="M4 3.2 L5.2 3 L5.6 4.6 L4.9 5.2 Q5.6 6.7 6.9 7.3 L7.5 6.6 L9 7 L8.8 8.3 Q5.5 8.8 3.7 4.6 Z"/></svg>
        123-456-0789
      </li>
      <li>
        <svg class="contact-icon" viewBox="0 0 12 12" aria-label="Fax"><rect x="3" y="1" width="6" height="4"/><rect x="0.5" y="5" width="11" height="6" rx="1"/></svg>
        123-456-0789
      </li>
      <li>
        <svg class="contact-icon" viewBox="0 0 12 12" aria-label="Email"><rect x="0.5" y="3" width="11" height="7.5" rx="1"/><path d="M1 3.5 L6 7 L11 3.5" fill="none" stroke="#fff" stroke-width="1"/></svg>
        info@brightwellpower.ca
      </li>
      <li>
        <svg class="contact-icon" viewBox="0 0 12 12" aria-label="Website"><circle cx="6" cy="6" r="5.5"/><path d="M0.5 6 H11.5 M6 0.5 V11.5 M1.5 3.5 H10.5 M1.5 8.5 H10.5" stroke="#fff" stroke-width="0.7" fill="none"/><ellipse cx="6" cy="6" rx="2.4" ry="5.5" fill="none" stroke="#fff" stroke-width="0.7"/></svg>
        www.brightwellpower.ca
      </li>
    </ul>
  </header>

  <svg class="footer-band" viewBox="0 0 1011 21" preserveAspectRatio="none" aria-hidden="true">
    <polygon points="0,0 525,0 500,21 0,21" fill="var(--brand-blue)"/>
    <polygon points="542,0 1011,0 1011,21 516,21" fill="var(--band-grey)"/>
  </svg>
</main>
</body>
</html>
```